Business Card Design Project

Lorabelle is a women fashion house focusing on youthful glamour.

We bring together unique designs, premium quality materials and top craftsmanship to deliver sophisticated yet playful glamour, fun and excitement to the confident woman.

We can sum up the brand identity in 3 words:
Glamour – Sophistication – Unique

Industry/Entity Type

Fashion

Requirements
Must have
• Nim Ferrasco
nim.ferrasco@lorabelle-example.com
Mobile: 081 536 2947
Instragram: lorabelle_label
Facebook: lorabelle

Creative Director
Lorabelle Co., LTD
TEL: 02 631 48 97
42 Maple Row, 2nd Floor , D Building , Thonrak , Chaloemrat 28.
East Sanphet , Rattana , Bangkok 10240 Thailand
www.lorabelle-example.com

```html
<!DOCTYPE html>
<html lang="en">
<head>
<meta charset="utf-8">
<title>Lorabelle Co., LTD – Business Card</title>
<link rel="stylesheet" href="https://fonts.googleapis.com/css2?family=Tinos&family=Work+Sans:wght@400;500&display=swap">
<style>
  :root {
    --page: #e9e6e1;
    --paper-light: #f7f7f7;
    --paper-mid: #dcdcdc;
    --ink: #3a3a3a;
    --ink-soft: #555555;
    --rule: #6a6a6a;
    --band-dark: #2b2b2b;
    --band-mid: #4a4a4a;
    --pattern-dark: #2e2e2e;
    --pattern-mid: #4b4b4b;
    --on-dark: #e6e6e6;
    --band-light: #ececec;
  }
  * { box-sizing: border-box; margin: 0; padding: 0; }
  html, body { width: 1200px; height: 1023px; overflow: hidden; }
  body {
    background: var(--page);
    font-family: "Work Sans", Arial, sans-serif;
    color: var(--ink);
    position: relative;
  }
  .card {
    position: absolute;
    top: 160px;
    width: 400px;
    height: 700px;
    overflow: hidden;
    box-shadow: 0 10px 30px rgba(0,0,0,.25);
  }
  .card--front { left: 150px; background: radial-gradient(ellipse at 50% 35%, var(--paper-light), var(--paper-mid)); }
  .card--back { left: 650px; background: var(--pattern-dark); }

  .wordmark { font-family: "Tinos", "Times New Roman", serif; color: var(--ink); line-height: 1; }
  .wordmark__name { display: block; font-size: 74px; letter-spacing: 1px; }
  .wordmark__suffix { display: block; text-align: right; font-size: 22px; margin-top: -2px; }

  .card--front .wordmark { position: absolute; top: 70px; left: 36px; right: 32px; }

  .contact { position: absolute; top: 230px; left: 36px; right: 36px; font-size: 15px; }
  .contact__name { text-align: right; font-size: 26px; font-weight: 400; letter-spacing: 1px; }
  .contact__title { text-align: right; font-size: 14px; color: var(--ink-soft); margin-top: 2px; }
  .contact__rule { border: 0; border-top: 1px solid var(--rule); margin: 12px 0; }
  .contact__row { display: flex; align-items: center; justify-content: flex-end; gap: 8px; margin: 6px 0; }
  .contact__row svg { width: 16px; height: 16px; fill: var(--ink-soft); flex: none; }
  .contact__address { display: flex; gap: 8px; line-height: 1.45; font-size: 14.5px; }
  .contact__address svg { width: 16px; height: 18px; fill: var(--ink-soft); flex: none; margin-top: 2px; }

  .social-band {
    position: absolute; left: 0; right: 0; bottom: 0; height: 72px;
    background: linear-gradient(90deg, var(--band-dark), var(--band-mid) 60%, var(--band-dark));
    color: var(--on-dark);
    display: flex; align-items: center; justify-content: space-between;
    padding: 0 24px; font-size: 15px;
  }
  .social { display: flex; align-items: center; gap: 8px; }
  .social__dot { width: 16px; height: 16px; border-radius: 50%; background: var(--on-dark); }
  .social__square { width: 16px; height: 16px; background: var(--on-dark); }

  .pattern-area {
    position: absolute; left: 0; right: 0; top: 0; height: 500px;
    background: radial-gradient(ellipse at 40% 40%, var(--pattern-mid), var(--pattern-dark));
  }
  .tagline {
    position: absolute; top: 300px; left: 0; right: 0;
    text-align: center; color: var(--on-dark);
    font-size: 26px; letter-spacing: 2px; line-height: 1.35;
  }
  .brand-band {
    position: absolute; left: 0; right: 0; top: 500px; height: 130px;
    background: linear-gradient(180deg, #f5f5f5, var(--band-light) 60%, #cfcfcf);
    padding: 24px 34px 0 48px;
  }
  .brand-band .wordmark__name { font-size: 68px; }
  .brand-band .wordmark__suffix { font-size: 20px; margin-top: -4px; }
  .url-strip {
    position: absolute; left: 0; right: 0; bottom: 0; height: 70px;
    background: linear-gradient(180deg, var(--band-mid), var(--band-dark));
    color: var(--on-dark); font-size: 15px; letter-spacing: 1px;
    display: flex; align-items: center; justify-content: center;
  }
</style>
</head>
<body>

<section class="card card--front" aria-label="Business card front">
  <div class="wordmark">
    <span class="wordmark__name">Lorabelle</span>
    <span class="wordmark__suffix">Co., LTD</span>
  </div>

  <div class="contact">
    <h1 class="contact__name">NIM FERRASCO</h1>
    <p class="contact__title">Creative Director</p>
    <hr class="contact__rule">
    <p class="contact__row">
      <svg viewBox="0 0 16 16" aria-hidden="true"><path d="M1 5c0-2 3-3 7-3s7 1 7 3v1h-4V5H5v1H1zM3 7h10l1 7H2z"/></svg>
      02 631 48 97
    </p>
    <p class="contact__row">
      <svg viewBox="0 0 16 16" aria-hidden="true"><path d="M5 1h6a1 1 0 0 1 1 1v12a1 1 0 0 1-1 1H5a1 1 0 0 1-1-1V2a1 1 0 0 1 1-1zm0 2v8h6V3z"/></svg>
      081 536 2947
    </p>
    <hr class="contact__rule">
    <p class="contact__row">
      <svg viewBox="0 0 16 16" aria-hidden="true"><path d="M1 3h14v10H1zm1.5 1.5L8 9l5.5-4.5z" fill-rule="evenodd"/></svg>
      nim.ferrasco@lorabelle-example.com
    </p>
    <p class="contact__row">
      <svg viewBox="0 0 16 16" aria-hidden="true"><path d="M8 1a7 7 0 1 0 0 14A7 7 0 0 0 8 1zm0 1.5c.8 0 1.7 1.6 2 4H6c.3-2.4 1.2-4 2-4zM5.9 8h4.2c0 .5-.1 1-.1 1.5H6c0-.5-.1-1-.1-1.5zM2.6 6.5h2c-.1.5-.1 1-.1 1.5s0 1 .1 1.5h-2a5.5 5.5 0 0 1 0-3zm8.8 0h2a5.5 5.5 0 0 1 0 3h-2c.1-.5.1-1 .1-1.5s0-1-.1-1.5zM6 11h4c-.3 1.6-1.2 2.5-2 2.5s-1.7-.9-2-2.5z"/></svg>
      www.lorabelle-example.com
    </p>
    <hr class="contact__rule">
    <p class="contact__address">
      <svg viewBox="0 0 16 18" aria-hidden="true"><path d="M8 0a6 6 0 0 1 6 6c0 4.5-6 12-6 12S2 10.5 2 6a6 6 0 0 1 6-6zm0 3.5a2.5 2.5 0 1 0 0 5 2.5 2.5 0 0 0 0-5z"/></svg>
      <span>42 Maple Row, 2nd Floor , D Building , Thonrak , Chaloemrat 28.<br>East Sanphet , Rattana , Bangkok 10240 Thailand</span>
    </p>
  </div>

  <footer class="social-band">
    <span class="social"><span class="social__dot" aria-hidden="true"></span>lorabelle_label</span>
    <span class="social"><span class="social__square" aria-hidden="true"></span>lorabelle</span>
  </footer>
</section>

<section class="card card--back" aria-label="Business card back">
  <div class="pattern-area" role="img" aria-label="Dark grey damask floral pattern"></div>
  <p class="tagline">Glamour<br>Sophistication<br>Unique</p>
  <div class="brand-band">
    <div class="wordmark">
      <span class="wordmark__name">Lorabelle</span>
      <span class="wordmark__suffix">Co., LTD</span>
    </div>
  </div>
  <footer class="url-strip">www.lorabelle-example.com</footer>
</section>

</body>
</html>
```